Website Design for Wheels for Servicemen.org - Donated Cars to Disabled Vets

Need a Wordpress website. The coding now, esp. the CDONT coding is not supported by many hosting sites. Looking for a landing page to generate leads.

Logo Text

look at current one for ideas

Coding

Coded - Design and coding required

Number of Pages Required

1 page

Requirements
Must have
• look at current website at www.wheelsforservicemen.org
Nice to have
• look at this site: http://givevehicletoservicemen.org

```html
<!DOCTYPE html>
<html lang="en">
<head>
<meta charset="utf-8">
<title>Wheels for Servicemen – Donate Your Car</title>
<link rel="stylesheet" href="https://fonts.googleapis.com/css2?family=Roboto:wght@400;500;700&family=Open+Sans:wght@400;600;700&display=swap">
<style>
:root{
  --blue:#1d5cb4;
  --blue-dark:#123f85;
  --blue-band:#1f5fb8;
  --nav:#2b2f36;
  --red:#b71a11;
  --red-dark:#961209;
  --ink:#1e1e1e;
  --muted:#6d6d6d;
  --line:#d7d7d7;
  --gray-bg:#f1f1f1;
  --white:#fff;
}
*{box-sizing:border-box;margin:0;padding:0}
html,body{width:1200px;height:2497px;overflow:hidden;background:var(--white)}
body{position:relative;font-family:"Open Sans",Arial,sans-serif;color:var(--ink)}
.abs{position:absolute}
h1,h2,h3,.heading{font-family:"Roboto",Arial,sans-serif}

/* header */
.topbar{left:0;top:0;width:1200px;height:87px;background:linear-gradient(180deg,#2a6cc6,#1650a6)}
.brand{left:100px;top:24px;display:flex;align-items:center;gap:10px}
.brand-mark{width:34px;height:34px;background:var(--red);border-radius:4px}
.brand-name{font-family:"Roboto",Arial,sans-serif;font-size:20px;font-weight:500;color:var(--white)}
.search{left:416px;top:23px;width:300px;height:37px;background:var(--white);border-radius:5px;display:flex;align-items:center;justify-content:space-between;padding:0 14px;font-size:12px;color:#666}
.open-badge{left:758px;top:8px;width:70px;height:70px;border-radius:50%;background:#e0261b}
.callout{left:849px;top:10px;color:var(--white);font-family:"Roboto",Arial,sans-serif}
.callout .need{font-size:16px;font-weight:500}
.callout .call{font-size:20px;font-weight:500;margin-top:1px}
.callout .call b{font-weight:700}
.callout .live{font-size:12px;margin-top:3px}
.nav{left:0;top:87px;width:1200px;height:38px;background:var(--nav)}
.nav a{position:absolute;top:11px;font-family:"Roboto",Arial,sans-serif;font-size:14px;font-weight:500;color:var(--white);text-decoration:none}

/* hero */
.hero-photo{left:0;top:125px;width:1200px;height:429px;background:linear-gradient(90deg,#eeeeee 0%,#e4e2df 30%,#e9e9ea 60%,#f2f2f2 100%)}
.slider-arrow{top:308px;width:38px;height:62px;background:#b9bcc0;display:flex;align-items:center;justify-content:center}

/* donate form */
.donate-form{left:709px;top:88px;width:394px;height:466px;background:var(--white);box-shadow:0 0 6px rgba(0,0,0,.25)}
.donate-form .form-title{height:45px;background:var(--blue);color:var(--white);font-family:"Roboto",Arial,sans-serif;font-size:21px;font-weight:700;text-align:center;line-height:45px}
.donate-form .form-intro{position:absolute;left:20px;top:58px;font-size:13px;font-weight:600}
.donate-form .form-intro b{color:var(--red);font-size:16px;font-weight:700}
.fields{position:absolute;left:18px;top:100px;width:358px;display:grid;grid-template-columns:1fr 1fr;column-gap:7px;row-gap:16px}
.field label{display:block;font-size:12px;line-height:14px;color:#333;margin-bottom:3px}
.field .input{height:27px;border:1px solid #bdbdbd;background:var(--white);position:relative}
.field .select::after{content:"";position:absolute;right:0;top:0;width:24px;height:25px;border-left:1px solid #ccc}
.field .select::before{content:"";position:absolute;right:8px;top:10px;border:4px solid transparent;border-top:5px solid #666;z-index:1}
.btn-red{background:var(--red);color:var(--white);font-family:"Roboto",Arial,sans-serif;font-weight:700;text-align:center;border-radius:4px}
.donate-form .btn-red{position:absolute;left:18px;top:403px;width:358px;height:43px;line-height:43px;font-size:15px}

/* how it works */
.section-title{font-size:22px;font-weight:700;color:var(--ink)}
.how-title{left:0;top:620px;width:1200px;text-align:center}
.how-intro{left:200px;top:670px;width:800px;text-align:center;font-size:12px;line-height:22px;color:var(--muted)}
.step{top:764px;width:360px;text-align:center}
.step .ring{position:relative;width:212px;height:212px;margin:0 auto;border:1.5px solid #6c8fd0;border-radius:50%;display:flex;align-items:center;justify-content:center}
.step .num{position:absolute;right:2px;top:22px;width:34px;height:34px;border-radius:50%;background:var(--blue);color:var(--white);font-size:15px;line-height:34px;font-family:"Roboto",Arial,sans-serif}
.step h3{margin-top:19px;font-size:20px;font-weight:400}
.step p{margin-top:12px;font-size:12px;line-height:22px;color:var(--muted)}

/* why donate */
.why{left:0;top:1123px;width:1200px;height:488px;background:var(--gray-bg)}
.car-left{left:0;top:1198px;width:541px;height:333px;background:linear-gradient(90deg,#9e1a18 0%,#d12a25 55%,#e4e4e4 90%,#f1f1f1 100%)}
.why-title{left:601px;top:1178px}
.checklist{list-style:none}
.checklist li{position:relative;padding-left:26px;font-size:12.5px;line-height:22px;color:#555}
.checklist li svg{position:absolute;left:0;top:5px}
.why-list{left:601px;top:1236px;width:500px}
.why-list li{margin-bottom:16px}

/* donate today */
.today-title{left:100px;top:1655px}
.today-list{left:100px;top:1716px}
.today-list li{margin-bottom:13px}
.today-btn{left:100px;top:1915px;width:191px;height:44px;line-height:44px;font-size:15px}
.car-right{left:607px;top:1664px;width:593px;height:333px;background:linear-gradient(90deg,#ffffff 0%,#e6e6e6 10%,#c52521 40%,#a0171a 100%)}

/* program band */
.program{left:0;top:2030px;width:1200px;height:133px;background:var(--blue-band)}
.program-label{left:0;top:2030px;width:350px;height:133px}
.program-title{left:100px;top:2066px;color:var(--white);font-size:23px;font-weight:700;line-height:31px}
.feature{top:2056px;width:180px;text-align:center;color:var(--white);font-family:"Roboto",Arial,sans-serif;font-size:14px;line-height:20px}
.feature .icon{height:44px;display:flex;align-items:flex-end;justify-content:center;margin-bottom:6px}

/* footer */
.seal{left:166px;top:2203px;width:109px;height:88px;border-radius:50%;background:#d9dfe8;border:4px solid #7d95b8}
.secure{left:108px;top:2321px;width:225px;height:76px;background:#e8e8e8;border-radius:6px}
.foot-col h4{font-family:"Roboto",Arial,sans-serif;font-size:18px;font-weight:500;margin-bottom:14px}
.foot-links{list-style:none}
.foot-links li{font-size:12px;line-height:24px;color:#555}
.info-col{left:403px;top:2214px}
.news-col{left:577px;top:2214px;width:260px}
.news-col p{font-size:12px;line-height:20px;color:#555}
.news-input{margin-top:14px;width:255px;height:36px;border:1px solid #c8c8c8;font-size:11px;color:#999;padding:10px 12px}
.subscribe{margin-top:17px;width:90px;height:28px;border:1px solid #c8c8c8;color:var(--red);font-size:11px;font-weight:700;text-align:center;line-height:26px}
.contact-col{left:899px;top:2214px;width:260px}
.contact-item{position:relative;padding-left:26px;font-size:12px;line-height:22px;color:#555;margin-bottom:25px}
.contact-item svg{position:absolute;left:2px;top:4px}
.foot-rule{left:100px;top:2440px;width:1000px;height:1px;background:var(--line)}
.copyright{left:100px;top:2458px;font-size:12px;color:#444}
.social{top:2454px;width:30px;height:30px;border-radius:50%;border:1.5px solid var(--red)}
</style>
</head>
<body>

<!-- header -->
<div class="abs topbar"></div>
<div class="abs brand"><span class="brand-mark"></span><span class="brand-name">Wheels for Servicemen</span></div>
<div class="abs search"><span>SEARCH</span>
  <svg width="15" height="15" viewBox="0 0 16 16"><circle cx="6.5" cy="6.5" r="5" fill="none" stroke="#777" stroke-width="2"/><path d="M10.5 10.5L15 15" stroke="#777" stroke-width="2"/></svg>
</div>
<div class="abs open-badge"></div>
<div class="abs callout">
  <div class="need">We need your help</div>
  <div class="call">Call <b>1-800-555-0142</b></div>
  <div class="live">Live operator available 7 days a week</div>
</div>

<nav class="abs nav">
  <a style="left:100px">HOME</a>
  <a style="left:170px">ABOUT</a>
  <a style="left:248px">HOW IT WORKS</a>
  <a style="left:383px">CHARITIES</a>
  <a style="left:484px">TAX DEDUCTION</a>
  <a style="left:626px">FAQ</a>
</nav>

<!-- hero -->
<div class="abs hero-photo" role="img" aria-label="Smiling couple, the man in military uniform, holding up car keys beside two silver sedans"></div>
<div class="abs slider-arrow" style="left:0"><svg width="12" height="20" viewBox="0 0 12 20"><path d="M10 2L2 10l8 8" fill="none" stroke="#fff" stroke-width="2.5"/></svg></div>
<div class="abs slider-arrow" style="left:1162px"><svg width="12" height="20" viewBox="0 0 12 20"><path d="M2 2l8 8-8 8" fill="none" stroke="#fff" stroke-width="2.5"/></svg></div>

<form class="abs donate-form">
  <div class="form-title">DONATE YOUR CAR</div>
  <div class="form-intro">Please fill out form or Call toll-free <b>1-800-555-0142</b></div>
  <div class="fields">
    <div class="field"><label>Name:</label><div class="input"></div></div>
    <div class="field"><label>Email:</label><div class="input"></div></div>
    <div class="field"><label>Phone:</label><div class="input"></div></div>
    <div class="field"><label>Cell Phone:</label><div class="input"></div></div>
    <div class="field"><label>Address:</label><div class="input"></div></div>
    <div class="field"><label>City:</label><div class="input"></div></div>
    <div class="field"><label>Choose Year:</label><div class="input select"></div></div>
    <div class="field"><label>Choose Model:</label><div class="input select"></div></div>
    <div class="field"><label>State:</label><div class="input select"></div></div>
    <div class="field"><label>Zip Code:</label><div class="input"></div></div>
  </div>
  <div class="btn-red">CLICK HERE TO DONATE NOW!</div>
</form>

<!-- how it works -->
<h2 class="abs section-title how-title">HOW IT WORKS</h2>
<p class="abs how-intro">Sed ut perspiciatis unde omnis iste natus error sit voluptatem accusantium doloremque laudantium, totam rem aperiam, eaque ipsa quae ab illo inventore vee vitae dicta sunt upernatur aut odconsequuntur magni dolores eos qui ratione voluptatem sequi</p>

<div class="abs step" style="left:55px">
  <div class="ring"><span class="num">1</span>
    <svg width="76" height="66" viewBox="0 0 76 66"><rect x="4" y="10" width="48" height="50" rx="6" fill="none" stroke="#b71a11" stroke-width="6"/><path d="M26 44l4-12 30-30 8 8-30 30z" fill="#b71a11"/><path d="M26 44l12-4" stroke="#fff" stroke-width="2"/></svg>
  </div>
  <h3>Fill out the simple form</h3>
  <p>Complete the form and a representative will call you<br>to arrange a convenient time to pickup your car.</p>
</div>
<div class="abs step" style="left:419px">
  <div class="ring"><span class="num">2</span>
    <svg width="68" height="70" viewBox="0 0 68 70"><rect x="3" y="8" width="62" height="59" rx="4" fill="none" stroke="#b71a11" stroke-width="5"/><rect x="3" y="8" width="62" height="12" fill="#b71a11"/><rect x="15" y="1" width="7" height="14" fill="#b71a11"/><rect x="46" y="1" width="7" height="14" fill="#b71a11"/><g fill="#b71a11"><rect x="11" y="27" width="9" height="8"/><rect x="24" y="27" width="9" height="8"/><rect x="37" y="27" width="9" height="8"/><rect x="50" y="27" width="9" height="8"/><rect x="11" y="39" width="9" height="8"/><rect x="24" y="39" width="9" height="8"/><rect x="37" y="39" width="9" height="8"/><rect x="50" y="39" width="9" height="8"/><rect x="11" y="51" width="9" height="8"/><rect x="24" y="51" width="9" height="8"/><rect x="37" y="51" width="9" height="8"/></g></svg>
  </div>
  <h3>Schedule your free pick-up</h3>
  <p>Complete the form and a representative will call you<br>to arrange a convenient time to pickup your car.</p>
</div>
<div class="abs step" style="left:782px">
  <div class="ring"><span class="num">3</span>
    <svg width="76" height="58" viewBox="0 0 76 58"><rect x="0" y="0" width="76" height="58" rx="6" fill="#b71a11"/><path d="M4 6l34 26 34-26" fill="none" stroke="#fff" stroke-width="3"/></svg>
  </div>
  <h3>Receive tax deduction</h3>
  <p>Complete the form and a representative will call you<br>to arrange a convenient time to pickup your car.</p>
</div>
<svg class="abs" style="left:386px;top:838px" width="68" height="60" viewBox="0 0 68 60"><path d="M2 4c18 2 40 14 58 40" fill="none" stroke="#aaa" stroke-width="2"/><path d="M50 44l10 2 0-12" fill="none" stroke="#aaa" stroke-width="2"/></svg>
<svg class="abs" style="left:748px;top:838px" width="68" height="60" viewBox="0 0 68 60"><path d="M2 56c14-26 34-40 58-44" fill="none" stroke="#aaa" stroke-width="2"/><path d="M50 4l10 8-8 10" fill="none" stroke="#aaa" stroke-width="2"/></svg>

<!-- why donate -->
<div class="abs why"></div>
<div class="abs car-left" role="img" aria-label="Front of a red sedan facing right"></div>
<h2 class="abs section-title why-title">WHY DONATE YOUR CAR TO US?</h2>
<ul class="abs checklist why-list">
  <li><svg width="14" height="14" viewBox="0 0 14 14"><circle cx="7" cy="7" r="7" fill="#1d5cb4"/><path d="M3.5 7l2.5 2.5 4.5-5" fill="none" stroke="#fff" stroke-width="2"/></svg>IRS 501(c)3 Approved: Free 24/7 Pickup with No DMV Hassles.</li>
  <li><svg width="14" height="14" viewBox="0 0 14 14"><circle cx="7" cy="7" r="7" fill="#1d5cb4"/><path d="M3.5 7l2.5 2.5 4.5-5" fill="none" stroke="#fff" stroke-width="2"/></svg>Free Local Towing to You: We will pick up your car donation, running or not,<br>when it's most convenient, at home or work.</li>
  <li><svg width="14" height="14" viewBox="0 0 14 14"><circle cx="7" cy="7" r="7" fill="#1d5cb4"/><path d="M3.5 7l2.5 2.5 4.5-5" fill="none" stroke="#fff" stroke-width="2"/></svg>All Cars Accepted: We take your car regardless of its condition or<br>registration status.</li>
  <li><svg width="14" height="14" viewBox="0 0 14 14"><circle cx="7" cy="7" r="7" fill="#1d5cb4"/><path d="M3.5 7l2.5 2.5 4.5-5" fill="none" stroke="#fff" stroke-width="2"/></svg>Income Tax Deduction: We issue you an IRS tax receipt &amp; offer the largest<br>resale net</li>
  <li><svg width="14" height="14" viewBox="0 0 14 14"><circle cx="7" cy="7" r="7" fill="#1d5cb4"/><path d="M3.5 7l2.5 2.5 4.5-5" fill="none" stroke="#fff" stroke-width="2"/></svg>No Paperwork Hassles: We take any car and handle everything: DMV, Smog and<br>IRS paperwork.</li>
  <li><svg width="14" height="14" viewBox="0 0 14 14"><circle cx="7" cy="7" r="7" fill="#1d5cb4"/><path d="M3.5 7l2.5 2.5 4.5-5" fill="none" stroke="#fff" stroke-width="2"/></svg>Car donations help fund programs: And benefit National Servicemen Support<br>Fund.</li>
</ul>

<!-- donate today -->
<h2 class="abs section-title today-title">DONATE YOUR CAR TODAY!</h2>
<ul class="abs checklist today-list">
  <li><svg width="14" height="14" viewBox="0 0 14 14"><circle cx="7" cy="7" r="7" fill="#1d5cb4"/><path d="M3.5 7l2.5 2.5 4.5-5" fill="none" stroke="#fff" stroke-width="2"/></svg>You have no costs.</li>
  <li><svg width="14" height="14" viewBox="0 0 14 14"><circle cx="7" cy="7" r="7" fill="#1d5cb4"/><path d="M3.5 7l2.5 2.5 4.5-5" fill="none" stroke="#fff" stroke-width="2"/></svg>Free towing, running or not.</li>
  <li><svg width="14" height="14" viewBox="0 0 14 14"><circle cx="7" cy="7" r="7" fill="#1d5cb4"/><path d="M3.5 7l2.5 2.5 4.5-5" fill="none" stroke="#fff" stroke-width="2"/></svg>We issue you an IRS tax receipt.</li>
  <li><svg width="14" height="14" viewBox="0 0 14 14"><circle cx="7" cy="7" r="7" fill="#1d5cb4"/><path d="M3.5 7l2.5 2.5 4.5-5" fill="none" stroke="#fff" stroke-width="2"/></svg>We take care of all paperwork.</li>
  <li><svg width="14" height="14" viewBox="0 0 14 14"><circle cx="7" cy="7" r="7" fill="#1d5cb4"/><path d="M3.5 7l2.5 2.5 4.5-5" fill="none" stroke="#fff" stroke-width="2"/></svg>And we take care of DMV &amp; Smog issues.</li>
</ul>
<div class="abs btn-red today-btn">DONATE NOW!</div>
<div class="abs car-right" role="img" aria-label="Rear three-quarter view of a red sedan"></div>

<!-- program band -->
<div class="abs program"></div>
<svg class="abs program-label" viewBox="0 0 350 133"><path d="M0 0H290L350 66.5 290 133H0z" fill="#123f85"/></svg>
<div class="abs program-title heading">CAR DONATION<br>PROGRAM</div>
<div class="abs feature" style="left:351px"><div class="icon"><svg width="36" height="36" viewBox="0 0 36 36"><circle cx="18" cy="18" r="17" fill="#fff"/><path d="M8 10c4 1 6 4 5 8 3 1 4 5 2 8M22 5c-1 4 2 6 5 6 2 3 0 7-3 9 0 3 1 5 3 6" fill="none" stroke="#1f5fb8" stroke-width="3"/></svg></div>Donation Accepted<br>Nationalwide</div>
<div class="abs feature" style="left:554px"><div class="icon"><svg width="44" height="36" viewBox="0 0 44 36"><path d="M8 14l5-11h18l5 11h4v14h-4v6h-6v-6H14v6H8v-6H4V14z" fill="#fff"/><rect x="14" y="6" width="16" height="8" fill="#1f5fb8"/><circle cx="11" cy="21" r="3" fill="#1f5fb8"/><circle cx="33" cy="21" r="3" fill="#1f5fb8"/></svg></div>All Vehicle<br>Type welcome</div>
<div class="abs feature" style="left:759px"><div class="icon"><svg width="30" height="40" viewBox="0 0 30 40"><path d="M0 0h20l10 10v30H0z" fill="#fff"/><g stroke="#1f5fb8" stroke-width="2.5"><path d="M6 18h18M6 24h18M6 30h18"/></g></svg></div><br>Tax Deductible</div>
<div class="abs feature" style="left:962px"><div class="icon"><svg width="38" height="38" viewBox="0 0 38 38"><circle cx="19" cy="19" r="18" fill="#fff"/><path d="M10 19l6 6 12-13" fill="none" stroke="#1f5fb8" stroke-width="4"/></svg></div><br>Towing is Free</div>

<!-- footer -->
<div class="abs seal"></div>
<div class="abs secure"></div>

<div class="abs foot-col info-col">
  <h4>Information</h4>
  <ul class="foot-links"><li>Home</li><li>About</li><li>How It Works</li><li>Charities</li><li>Tax Deduction</li><li>FAQ</li></ul>
</div>
<div class="abs foot-col news-col">
  <h4>Newsletter Subscription</h4>
  <p>Register your Email Address to get<br>information about us</p>
  <div class="news-input">Email Address</div>
  <div class="subscribe">SUBSCRIBE</div>
</div>
<div class="abs foot-col contact-col">
  <h4>Contact Us</h4>
  <div class="contact-item"><svg width="10" height="14" viewBox="0 0 10 14"><path d="M5 14C1 8 0 6.5 0 5a5 5 0 0110 0c0 1.5-1 3-5 9z" fill="#b71a11"/><circle cx="5" cy="5" r="2" fill="#fff"/></svg>P.O Box 214, Harbor Road<br>Port Willow</div>
  <div class="contact-item"><svg width="12" height="12" viewBox="0 0 12 12"><path d="M2 0l3 3-1.5 2a7 7 0 003.5 3.5L9 7l3 3-2 2C5 12 0 7 0 2z" fill="#b71a11"/></svg>1-800-555-0142</div>
  <div class="contact-item"><svg width="13" height="10" viewBox="0 0 13 10"><rect width="13" height="10" fill="#b71a11"/><path d="M1 1l5.5 4.5L12 1" fill="none" stroke="#fff" stroke-width="1.3"/></svg>info@wheelsforservicemen.org</div>
</div>

<div class="abs foot-rule"></div>
<div class="abs copyright">Copyrights © 2016, Wheels for Servicemen. All rights reserved.</div>
<div class="abs social" style="left:968px"></div>
<div class="abs social" style="left:1003px"></div>
<div class="abs social" style="left:1038px"></div>
<div class="abs social" style="left:1073px"></div>

</body>
</html>
```